Storm Restoration Contractor needs a professional letterhead design

Looking for a professional letterhead design. Not looking for your cheapo MS Word standard ones that are readily available. Dont want it to be cookie cutter look like ones readily available online. We just recently changed our logo and want to freshen up all our documents. Our company handles restoring a property back to a pre-loss condition after a storm damages it. For example, wind, hail, flood, fire losses.

Target Market(s)

Property Owners, Homeowners, Property Owners, Commercial Property Owners, Property Management Companies

Industry/Entity Type

Construction Company

Requirements
Must have
• Professional, Use 1 of 2 logo options
• Storm Restoration, Roofing, Siding, Windows

```html
<!DOCTYPE html>
<html lang="en">
<head>
<meta charset="utf-8">
<title>Restora Shield Letterhead</title>
<link href="https://fonts.googleapis.com/css2?family=Questrial&display=swap" rel="stylesheet">
<style>
  :root {
    --backdrop: #b9b9b9;
    --paper: #f1f1f1;
    --ink: #2b2b2b;
    --brand-blue: #2169b3;
    --brand-grey: #4a4a4c;
    --signature-ink: #5b7fc7;
  }
  html, body {
    margin: 0;
    width: 1200px;
    height: 1041px;
    overflow: hidden;
    background: var(--backdrop);
    font-family: "Questrial", "Century Gothic", sans-serif;
    color: var(--ink);
  }
  .letterhead {
    position: absolute;
    left: 212px;
    top: 20px;
    width: 775px;
    height: 1000px;
    background: var(--paper);
    box-shadow: 0 2px 6px rgba(0,0,0,.25);
    overflow: hidden;
  }
  .brand {
    position: absolute;
    left: 64px;
    top: 60px;
    display: flex;
    align-items: center;
    gap: 12px;
  }
  .brand-dot {
    width: 62px;
    height: 62px;
    border-radius: 50%;
    border: 5px solid var(--brand-blue);
    box-sizing: border-box;
  }
  .brand-name {
    font-size: 30px;
    line-height: 1;
    color: var(--brand-blue);
    letter-spacing: 1px;
    text-transform: uppercase;
  }
  .contact {
    position: absolute;
    left: 571px;
    top: 56px;
    font-size: 10px;
    line-height: 13.5px;
  }
  .contact-row { display: flex; align-items: center; gap: 6px; }
  .contact-row svg { width: 10px; height: 10px; flex: none; }
  .contact-address { margin-top: 7px; }
  .letter {
    position: absolute;
    left: 64px;
    top: 226px;
    width: 647px;
    font-size: 11px;
    line-height: 13.6px;
  }
  .letter p { margin: 0 0 13.6px; text-align: justify; }
  .date { margin-bottom: 14px !important; }
  .recipient { margin-bottom: 54px !important; text-align: left !important; }
  .salutation { font-weight: bold; margin-bottom: 14px !important; }
  .closing {
    margin-top: 28px;
    display: flex;
    align-items: flex-start;
    gap: 12px;
  }
  .signer { font-weight: bold; }
  .signature {
    width: 160px;
    height: 80px;
    margin-top: -14px;
    background: linear-gradient(90deg, rgba(91,127,199,.18), rgba(91,127,199,.06));
    border-radius: 4px;
  }
  .footer-band {
    position: absolute;
    left: 0;
    bottom: 0;
    width: 775px;
    height: 22px;
  }
</style>
</head>
<body>
  <main class="letterhead">
    <header>
      <div class="brand">
        <div class="brand-dot"></div>
        <div class="brand-name">Restora Shield</div>
      </div>
      <address class="contact" style="font-style:normal">
        <div class="contact-row">
          <svg viewBox="0 0 10 10"><rect width="10" height="10" rx="2" fill="var(--brand-blue)"/><path d="M3 2.5c-.6.4-.6 1.4 0 2.6s1.6 2.1 2.6 2.4c.6.1 1-.2 1.3-.6L5.9 6l-.6.5C4.6 6.2 3.9 5.4 3.6 4.7l.5-.6L3 2.5z" fill="#fff"/></svg>
          <span>555-014-2290</span>
        </div>
        <div class="contact-row">
          <svg viewBox="0 0 10 10"><rect width="10" height="10" rx="2" fill="var(--brand-blue)"/><rect x="2" y="3" width="6" height="4" fill="none" stroke="#fff" stroke-width=".8"/><path d="M2 3l3 2.2L8 3" fill="none" stroke="#fff" stroke-width=".8"/></svg>
          <span>info@restorashield.com</span>
        </div>
        <div class="contact-row">
          <svg viewBox="0 0 10 10"><rect width="10" height="10" rx="2" fill="var(--brand-blue)"/><circle cx="5" cy="5" r="3" fill="none" stroke="#fff" stroke-width=".7"/><path d="M2 5h6M5 2c-1.5 2-1.5 4 0 6M5 2c1.5 2 1.5 4 0 6" fill="none" stroke="#fff" stroke-width=".6"/></svg>
          <span>www.restorashield.com</span>
        </div>
        <div class="contact-address">4120 E Canyon Ridge Rd STE 210<br>Mesa, AZ 85213</div>
      </address>
    </header>

    <section class="letter">
      <p class="date">30.11.2016</p>
      <p class="recipient">Recipient's name<br>Lindenweg 7<br>10115 Berlin<br>Germany</p>
      <p class="salutation">Dear sir,</p>
      <p>Communication is a very integral part of living creatures, animals and humans. Communication may be verbal or written. Written communication however is only applicable to human beings. Can you even imagine a world without communication? Verbal communication can be through telephones, webcams or in person. Written communication is through letters, emails and mobile phone messages.</p>
      <p>In today's world of great inventions and technology, letters have somehow become redundant. It is the time for text messages or chats. But they still can communicate a lot more than all other modes of communication. Organizations and various government departments still bank on letters as a strong medium of communication. There is no comparison in costs of sending letters as compared to costs of mobile phone messages though – letters are far cheaper. Letters now commonly known as “hard copy documents” are considered more relevant and important than email copies of text messages as proof or evidence of some sort.</p>
      <p>Letters speak volumes about a person or an organization that writes it. So one must take utmost care ensuring that the language used in any letter is appropriate for the occasion for which it is being written. Since a letter is also a written proof or document, if there are certain things that should not form a part of it, then that too should be carefully handled.</p>
      <p>Writing a good letter is an art. But if for some reason someone is unable to write that perfect letter, these different types of letters provide a base for you to build on. Sample letters have been given for everyone to understand what all information needs to form a part of the letter type and then it can be customized.</p>
      <div class="closing">
        <div>Yours Sincerely,<br><span class="signer">Lena Hartwig</span></div>
        <div class="signature" role="img" aria-label="Handwritten signature in blue ink"></div>
      </div>
    </section>

    <svg class="footer-band" viewBox="0 0 775 22" preserveAspectRatio="none" aria-hidden="true">
      <polygon points="0,8 510,8 499,22 0,22" fill="var(--brand-grey)"/>
      <polygon points="517,8 520,8 509,22 506,22" fill="#ffffff"/>
      <polygon points="528,0 775,0 775,22 510,22" fill="var(--brand-blue)"/>
    </svg>
  </main>
</body>
</html>
```